Now Leasing Banner

Looking for a banner that says the following information approx 4' x 30'

Now Leasing Maplebrook Terrace 925-318-6042

Target Market(s)

Drive by traffic

Industry/Entity Type

Residential property management

Requirements
Must have
• Clear and readable from a distance

```html
<!DOCTYPE html>
<html lang="en">
<head>
<meta charset="utf-8">
<title>Now Leasing Banner – Maplebrook Terrace</title>
<link rel="stylesheet" href="https://fonts.googleapis.com/css2?family=Barlow+Condensed:wght@800&family=Barlow+Semi+Condensed:wght@700&display=swap">
<style>
  :root {
    --banner-yellow: #f8d70a;
    --headline-black: #0d0d0d;
    --phone-red: #ae1e25;
    --outline-white: #ffffff;
  }
  html, body {
    margin: 0;
    padding: 0;
    width: 1200px;
    height: 160px;
    overflow: hidden;
  }
  .banner {
    position: relative;
    width: 1200px;
    height: 160px;
    background: var(--banner-yellow);
    overflow: hidden;
  }
  .headline {
    position: absolute;
    left: 34px;
    top: 8px;
    margin: 0;
    font-family: "Barlow Condensed", "Arial Narrow", sans-serif;
    font-weight: 800;
    font-size: 70px;
    line-height: 69px;
    letter-spacing: 0.5px;
    text-transform: uppercase;
    color: var(--headline-black);
  }
  .headline span {
    display: block;
  }
  .phone-pill {
    position: absolute;
    left: 619px;
    top: 23px;
    width: 640px;
    height: 114px;
    border-radius: 57px 0 0 57px;
    background: var(--outline-white);
  }
  .phone-pill__inner {
    position: absolute;
    left: 11px;
    top: 9px;
    right: 0;
    bottom: 9px;
    border-radius: 48px 0 0 48px;
    background: var(--phone-red);
  }
  .phone-number {
    position: absolute;
    left: 670px;
    top: 32px;
    width: 496px;
    height: 96px;
    display: flex;
    align-items: center;
    justify-content: center;
    font-family: "Barlow Semi Condensed", "Arial Narrow", sans-serif;
    font-weight: 700;
    font-size: 72px;
    letter-spacing: 2px;
    color: var(--outline-white);
    text-decoration: none;
  }
</style>
</head>
<body>
  <div class="banner">
    <h1 class="headline">
      <span class="headline__status">Now Leasing</span>
      <span class="headline__property">Maplebrook Terrace</span>
    </h1>
    <div class="phone-pill">
      <div class="phone-pill__inner"></div>
    </div>
    <a class="phone-number" href="tel:9253186042">925-318-6042</a>
  </div>
</body>
</html>
```